BUSINESS CARD DESIGN

NAME- DALE VORSKIN
PHONE NUMER - 555- 714-9082
EMAIL- OFFICE@TRV-GROUNDMAKRZ.COM
BACK OF CARD- SPEACIALIZES IN LAND CLEARING, FORESTRY MUCLHING AND EXCAVATION

Contact Information for Business Card

NAME- DALE VORSKIN PHONE NUMER - 555- 714-9082 EMAIL- OFFICE@TRV-GROUNDMAKRZ.COM BACK OF CARD- SPEACIALIZES IN LAND CLEARING , MUCLHING AND EXCAVATION

```html
<!DOCTYPE html>
<html lang="en">
<head>
<meta charset="utf-8">
<title>Traverse Ground Makrz – Business Card</title>
<link href="https://fonts.googleapis.com/css2?family=Audiowide&family=Roboto:wght@400;500&display=swap" rel="stylesheet">
<style>
  :root {
    --canvas: #1b1c1e;
    --card: #262628;
    --card-dark: #1f1f21;
    --gold: #ffc20e;
    --edge: #ff9a1a;
    --white: #f4f4f4;
    --pattern-a: #2c2c2e;
    --pattern-b: #3a3a3c;
  }
  * { box-sizing: border-box; margin: 0; padding: 0; }
  html, body { width: 1200px; height: 840px; overflow: hidden; background: var(--canvas); }
  .canvas {
    width: 1200px; height: 840px;
    display: flex; flex-direction: column; align-items: center; justify-content: center; gap: 36px;
  }
  .card {
    position: relative;
    width: 660px; height: 377px;
    border-radius: 26px;
    background: var(--card);
    border-bottom: 4px solid var(--edge);
    border-left: 2px solid var(--gold);
    overflow: hidden;
  }
  .wordmark {
    font-family: "Audiowide", sans-serif;
    color: var(--gold);
    text-align: center;
    line-height: 1.05;
    display: flex; align-items: center; gap: 14px;
  }
  .wordmark__dot { width: 58px; height: 58px; border-radius: 50%; background: var(--gold); flex: none; }
  .wordmark__lines { display: flex; flex-direction: column; }
  .wordmark__main { font-size: 26px; letter-spacing: 1px; }
  .wordmark__sub { font-size: 14px; letter-spacing: 8px; }
  .wordmark__place { font-size: 13px; letter-spacing: 10px; }
  .wordmark__rule { height: 3px; background: var(--gold); margin: 5px auto 0; width: 80%; }

  /* back */
  .card--back { background: var(--card-dark); }
  .card__pattern {
    position: absolute; inset: 0;
    background: linear-gradient(120deg, var(--pattern-a) 0%, var(--card-dark) 50%, var(--pattern-b) 100%);
  }
  .back__content {
    position: absolute; inset: 0;
    display: flex; flex-direction: column; align-items: center; justify-content: center; gap: 18px;
  }
  .badge {
    font-family: "Audiowide", sans-serif;
    background: var(--gold); color: var(--card-dark);
    font-size: 17px; letter-spacing: 1px; padding: 4px 12px;
  }
  .services {
    font-family: "Roboto", sans-serif; color: var(--white);
    font-size: 15px; letter-spacing: 0.5px;
    display: flex; gap: 10px; align-items: center;
  }
  .services__bullet { width: 7px; height: 7px; border-radius: 50%; background: var(--gold); }

  /* front */
  .front__brand { position: absolute; top: 70px; left: 0; right: 0; display: flex; justify-content: center; }
  .front__brand .wordmark__dot { width: 90px; height: 90px; }
  .front__footer {
    position: absolute; left: 40px; right: 40px; bottom: 52px;
    display: flex; align-items: center; gap: 24px;
  }
  .person { font-family: "Audiowide", sans-serif; color: var(--gold); font-size: 32px; letter-spacing: 1px; }
  .divider { width: 1px; height: 58px; background: var(--white); opacity: 0.8; }
  .contacts { display: flex; flex-direction: column; gap: 8px; font-family: "Roboto", sans-serif; color: var(--white); font-size: 17px; }
  .contact { display: flex; align-items: center; gap: 8px; }
  .contact svg { width: 18px; height: 18px; fill: var(--gold); flex: none; }
</style>
</head>
<body>
<main class="canvas">

  <section class="card card--back" aria-label="Card back">
    <div class="card__pattern" role="img" aria-label="Repeating tonal brand pattern across the card"></div>
    <div class="back__content">
      <div class="wordmark">
        <span class="wordmark__dot"></span>
        <div class="wordmark__lines">
          <span class="wordmark__main">TRAVERSE GROUND</span>
          <span class="wordmark__sub">MAKRZ LLC</span>
          <span class="wordmark__place">HAWAII</span>
          <span class="wordmark__rule"></span>
        </div>
      </div>
      <div class="badge">SPEACIALIZES IN</div>
      <div class="services">
        <span class="services__bullet"></span>LAND CLEARING
        <span class="services__bullet"></span>MUCLHING
        <span class="services__bullet"></span>EXCAVATION
      </div>
    </div>
  </section>

  <section class="card card--front" aria-label="Card front">
    <div class="front__brand">
      <div class="wordmark">
        <span class="wordmark__dot"></span>
        <div class="wordmark__lines">
          <span class="wordmark__main">TRAVERSE GROUND</span>
          <span class="wordmark__sub">MAKRZ LLC</span>
          <span class="wordmark__place">HAWAII</span>
          <span class="wordmark__rule"></span>
        </div>
      </div>
    </div>
    <div class="front__footer">
      <div class="person">DALE VORSKIN</div>
      <div class="divider"></div>
      <div class="contacts">
        <div class="contact">
          <svg viewBox="0 0 24 24" aria-hidden="true"><path d="M6.6 10.8a15 15 0 0 0 6.6 6.6l2.2-2.2c.3-.3.7-.4 1-.2 1.1.4 2.3.6 3.6.6.6 0 1 .4 1 1V20c0 .6-.4 1-1 1A17 17 0 0 1 3 4c0-.6.4-1 1-1h3.5c.6 0 1 .4 1 1 0 1.3.2 2.5.6 3.6.1.3 0 .7-.2 1z"/></svg>
          <span>555- 714-9082</span>
        </div>
        <div class="contact">
          <svg viewBox="0 0 24 24" aria-hidden="true"><path d="M2 5h20v14H2zm2 2v.5l8 5 8-5V7zm0 3v7h16v-7l-8 5z"/></svg>
          <span>office@trv-groundmakrz.com</span>
        </div>
      </div>
    </div>
  </section>

</main>
</body>
</html>
```